Machining Business Order Thank You Insert

I am looking for a business style card to include with orders that I ship. The card needs to thank the recipient for their order, and encourage them to leave a review. The card should include my business name and contact information and have an area to hand write a message.

I mainly sale on Craftlane and my own website. We are a machining an manufacturing business that are in the sale of mostly metal machined and 3d printed plastic products.

The front of the card should include the following:
Logo: (attached)
Snapgram: https://www.snapgram.example/kelvomill/
Friendsbook: https://www.friendsbook.example/KelvoMill
Website: https://www.kelvomill.example/

The back of the card needs an area to write a message

Industry/Entity Type

3D Printing, Machining, Craftlane

Contact Information for Business Card

Black or white front, white back to write a personal message

Font styles to use
Sans Serif

Colors

Designer to choose colors to be used in the design.

Requirements
Must have
• Encourage a review, social media info

```html
<!DOCTYPE html>
<html lang="en">
<head>
<meta charset="utf-8">
<title>KelvoMill – Order Thank You Card</title>
<link rel="stylesheet" href="https://fonts.googleapis.com/css2?family=Saira:wght@500&family=Arimo:wght@400&family=Dancing+Script:wght@600&display=swap">
<style>
  :root {
    --canvas-bg: #262626;
    --card-black: #050505;
    --card-white: #ffffff;
    --accent-orange: #ef6a2c;
    --rust: #6a2f1c;
    --contact-gray: #9a9a9a;
    --stripe-gray: #dcdcdc;
    --ink: #1c1c1c;
    --dot-gray: #6f6f6f;
    --review-gray: #555555;
  }
  * { box-sizing: border-box; margin: 0; padding: 0; }
  html, body {
    width: 1200px; height: 900px; overflow: hidden;
    background: var(--canvas-bg);
  }
  .canvas {
    position: relative; width: 1200px; height: 900px;
    display: flex; flex-direction: column; align-items: center; justify-content: center; gap: 36px;
  }
  .card {
    position: relative; width: 720px; height: 400px; overflow: hidden;
    box-shadow: 0 10px 30px rgba(0,0,0,.55);
  }

  /* Front */
  .card--front { background: var(--card-black); }
  .front-decoration {
    position: absolute; right: 0; top: 0; width: 330px; height: 100%;
    background: linear-gradient(120deg, rgba(106,47,28,0) 0%, rgba(106,47,28,.75) 45%, rgba(60,28,18,.6) 100%);
  }
  .brand {
    position: absolute; left: 56px; top: 190px;
    display: flex; align-items: center; gap: 16px;
  }
  .brand__square { width: 22px; height: 22px; background: var(--accent-orange); }
  .brand__name {
    font-family: "Saira", sans-serif; font-weight: 500; font-size: 30px;
    letter-spacing: 10px; color: var(--accent-orange);
  }
  .contacts {
    position: absolute; left: 60px; bottom: 40px; list-style: none;
    display: flex; flex-direction: column; gap: 6px;
  }
  .contacts__item {
    display: flex; align-items: center; gap: 16px;
    font-family: "Arimo", sans-serif; font-size: 17px; color: var(--contact-gray);
  }
  .contacts__dot { width: 13px; height: 13px; border-radius: 50%; background: var(--accent-orange); }

  /* Back */
  .card--back { background: var(--card-white); }
  .back-decoration {
    position: absolute; left: 0; top: 0; width: 320px; height: 100%;
    background: linear-gradient(135deg, var(--stripe-gray) 0%, #ececec 55%, rgba(255,255,255,0) 100%);
  }
  .thanks {
    position: absolute; right: 50px; top: 36px; text-align: right;
  }
  .thanks__title {
    font-family: "Dancing Script", cursive; font-weight: 600; font-size: 100px;
    line-height: 1; color: var(--ink);
  }
  .thanks__subtitle {
    font-family: "Dancing Script", cursive; font-weight: 600; font-size: 30px;
    color: var(--ink); margin-top: -6px; margin-right: 10px;
  }
  .write-lines {
    position: absolute; right: 40px; top: 204px; width: 360px;
    display: flex; flex-direction: column; gap: 28px;
  }
  .write-lines__line { border-top: 2px dotted var(--dot-gray); height: 0; }
  .review-note {
    position: absolute; right: 40px; bottom: 24px; width: 360px; text-align: right;
    font-family: "Arimo", sans-serif; font-size: 13px; color: var(--review-gray);
  }
</style>
</head>
<body>
<main class="canvas">
  <section class="card card--front">
    <div class="front-decoration" role="img" aria-label="Large rust-toned stacked line decoration"></div>
    <div class="brand">
      <span class="brand__square"></span>
      <span class="brand__name">KELVOMILL</span>
    </div>
    <ul class="contacts">
      <li class="contacts__item"><span class="contacts__dot"></span>@kelvomill</li>
      <li class="contacts__item"><span class="contacts__dot"></span>@kelvomill</li>
      <li class="contacts__item"><span class="contacts__dot"></span>www.kelvomill.example</li>
    </ul>
  </section>

  <section class="card card--back">
    <div class="back-decoration" role="img" aria-label="Faint grey stacked line decoration"></div>
    <div class="thanks">
      <p class="thanks__title">Thanks</p>
      <p class="thanks__subtitle">For Your Order!</p>
    </div>
    <div class="write-lines" aria-label="Space for a handwritten message">
      <div class="write-lines__line"></div>
      <div class="write-lines__line"></div>
      <div class="write-lines__line"></div>
      <div class="write-lines__line"></div>
      <div class="write-lines__line"></div>
    </div>
    <p class="review-note">Loved your order? Leave us a review on Craftlane!</p>
  </section>
</main>
</body>
</html>
```